Creation of a page for funnel

Our company is specialized in insoles and well-being. Our insoles help reduce joint problems, stress or ink to promote weight loss. We need a clean and refined sales page, this one will be used on funnel click. The page should display the values of our product in first: "promote weight loss" in second: "Relieves muscle and joint pain" third: "Increases energy and stress stress". The page must be in the colors of our logo (green) if possible this color: light green: dark green 54c248. It is important to follow this model for the page with totally new and fresh desing: https: // lunar-pebble. uk / qtw-lr Additionnal details for icons Section u: 1: "A unique design based on two types of knowledge" 2: "approved by acupressure expert" "Lose weight" 2: "Increases blood flow and oxygen in your body" 3: "Relieves muscle and joint pain" 4: "Increases energy and reduces stress" Section x: 1: "for men and women" 2: "one size "3:" Adjustable by cutting "Section y: 1:" powerful magnet in tourmaline "2:" for all type of shoes "3:" Flexible and light "4:" Breathable "Section z: 1:" free shipping "2 : "Customer service" 3: "money back guarantee" 4: "safe payment"
Target Market(s)
men and women 35
Number of Pages Required
1 page
Requirements
Must have
- the 5 sections mentioned in description
Nice to have
- some GIF like the funnel

```html
<!DOCTYPE html>
<html lang="en">
<head>
<meta charset="utf-8">
<title>StrideLeaf – Insoles</title>
<link rel="stylesheet" href="https://fonts.googleapis.com/css2?family=Lato:wght@400;700;900&display=swap">
<style>
:root{
  --green:#1f9a12;
  --green-text:#3aa317;
  --green-deep:#2e8f10;
  --dark:#333333;
  --ink:#222222;
  --muted:#444444;
  --panel:#f3f3f3;
  --red:#e31226;
  --orange:#fd7a0b;
  --blue:#27a9e8;
  --leaf:#22b24b;
}
*{box-sizing:border-box;margin:0;padding:0}
html,body{width:1200px;height:3231px;overflow:hidden}
body{position:relative;font-family:'Lato',sans-serif;color:var(--ink);background:#fff}
.abs{position:absolute}
.bg{position:absolute;left:0;top:0}

/* header */
.brand{position:absolute;display:flex;align-items:center;gap:10px}
.brand-dot{width:40px;height:40px;border-radius:50%;background:var(--green)}
.brand-name{font-weight:900;font-size:38px;color:var(--green);letter-spacing:1px;line-height:1}
.brand-tag{font-size:15px;color:var(--ink);font-weight:700;margin-top:2px}
.nav{position:absolute;top:46px;left:654px;display:flex;gap:38px;font-size:16px;font-weight:700;color:var(--ink)}
.btn{position:absolute;display:flex;align-items:center;justify-content:center;border-radius:22px;color:#fff;font-weight:700;font-size:16px}
.btn-green{background:var(--green);left:980px;top:37px;width:146px;height:42px}

/* hero */
.hero-photo{position:absolute;left:420px;top:110px;width:780px;height:540px;
  background:linear-gradient(100deg,rgba(31,154,18,0) 0%,#b8362f 14%,#2a2a2a 26%,#d9d9d6 42%,#a7a7a5 62%,#c9f23a 80%,#8e8e8a 100%);
  clip-path:polygon(0 0,100% 0,100% 95%,0 100%)}
.hero-title{left:75px;top:268px;font-size:66px;font-weight:700;color:#fff;letter-spacing:1px}
.hero-text{left:75px;top:346px;width:370px;font-size:19px;line-height:28px;color:#fff}
.btn-dark{left:75px;top:456px;width:146px;height:42px;background:#1b1b1b}

/* welcome */
.section-title{font-size:33px;font-weight:400;color:var(--ink)}
.welcome-title{left:0;width:1200px;top:728px;text-align:center}
.welcome-text{left:110px;width:980px;top:789px;text-align:center;font-size:16px;line-height:26px;color:var(--ink)}
.perk{position:absolute;top:878px;width:330px;text-align:center}
.perk svg{display:block;margin:0 auto 22px}
.perk p{font-size:19px;line-height:28px;color:var(--green-text)}

/* values */
.values-title{left:75px;top:1382px}
.values-text{left:75px;top:1437px;width:350px;font-size:14px;line-height:27px;color:var(--ink)}
.funnel{left:0;top:0}
.tier-label{position:absolute;text-align:right;font-weight:700;font-size:19px;line-height:28px}

/* cards */
.card{position:absolute;top:1915px;width:331px;text-align:center}
.card-img{width:331px;height:190px}
.card h3{margin-top:26px;font-size:19px;font-weight:900;color:var(--green-text);text-transform:uppercase}
.card p{margin-top:8px;font-size:14px;line-height:26px;color:var(--muted)}

/* features */
.features-title{left:73px;top:2395px}
.features-text{left:75px;top:2448px;width:570px;font-size:14px;line-height:27px;color:var(--ink)}
.feature{position:absolute;display:flex;align-items:center;gap:16px;font-weight:700;font-size:16px;line-height:20px;color:var(--green-text)}
.features-photo{position:absolute;left:660px;top:2355px;width:540px;height:402px;
  background:linear-gradient(160deg,#ffffff 0%,#f1d8c8 30%,#3b4a6a 58%,#2f7fd6 78%,#7fb6ef 100%)}

/* services band */
.band{left:0;top:2757px;width:1200px;height:278px;background:linear-gradient(90deg,#3a3a3a 0%,#3a5a24 45%,#3fa80f 100%)}
.service{position:absolute;top:2815px;width:270px;text-align:center;color:#fff}
.service svg{display:block;margin:0 auto 20px}
.service h4{font-size:21px;font-weight:900}
.service p{margin-top:6px;font-size:15px;line-height:25px;color:#e8e8e8}

/* footer */
.foot-copy{left:75px;top:3146px;font-size:12px;line-height:23px;color:var(--muted)}
.foot-col{position:absolute;top:3066px}
.foot-col h5{font-size:15px;font-weight:700;color:var(--ink);margin-bottom:8px}
.foot-col li{list-style:none;font-size:13px;line-height:28px;color:var(--muted);display:flex;align-items:center;gap:16px}
.socials{display:flex;gap:22px;margin-top:6px}
.socials span{width:18px;height:18px;border-radius:50%;background:#555}
.page-mark{left:1160px;top:3208px;font-size:12px;color:#2266cc}
</style>
</head>
<body>

<svg class="bg" width="1200" height="3231" aria-hidden="true">
  <polygon points="0,110 1200,110 1200,622 0,680" fill="#1f9a12"/>
  <polygon points="0,680 1200,622 1200,1135 0,1081" fill="#f3f3f3"/>
  <polygon points="0,1838 1200,1774 1200,2330 0,2302" fill="#f3f3f3"/>
</svg>

<!-- header -->
<div class="brand" style="left:75px;top:28px">
  <span class="brand-dot"></span>
  <div><div class="brand-name">StrideLeaf</div><div class="brand-tag">L’essayer c’est l’adopter !</div></div>
</div>
<nav class="nav"><span>How It Works</span><span>Pricing</span><span>FAQ</span></nav>
<a class="btn btn-green">Shop Now</a>

<!-- hero -->
<div class="hero-photo" role="img" aria-label="Photo of a red and black insole beside a person tying running shoes"></div>
<h1 class="abs hero-title">StrideLeaf</h1>
<p class="abs hero-text">Lorem ipsum dolor sit amet, consectetur adipiscing elitnam interdum ullamcorper quam tristique..</p>
<a class="btn btn-dark">Shop Now</a>

<!-- welcome -->
<h2 class="abs section-title welcome-title">Welcome to Our Wesite</h2>
<p class="abs welcome-text">Lorem ipsum dolor sit amet, consectetur adipiscing elit. Nam interdum ullamcorper quam, in tincidunt nibh commodo a. aliquam malesuada&nbsp; diam vel fermentum faucibus.</p>

<div class="perk" style="left:75px">
  <svg width="80" height="70" viewBox="0 0 80 70" fill="none" stroke="#3aa317" stroke-width="2.5"><path d="M6 60 C10 20 40 6 74 8 C72 40 48 62 14 58 Z"/><path d="M6 60 C24 44 40 34 58 24"/></svg>
  <p>A totally natural solution without any health risk</p>
</div>
<div class="perk" style="left:435px">
  <svg width="80" height="70" viewBox="0 0 80 70" fill="none" stroke="#3aa317" stroke-width="2.5"><rect x="4" y="30" width="16" height="34" rx="2"/><path d="M20 34 L34 30 L42 4 C50 4 52 12 50 24 L70 24 C76 26 76 32 72 34 C76 38 74 44 70 44 C74 48 72 54 68 54 C70 60 66 64 60 64 L20 62"/><circle cx="12" cy="56" r="2"/></svg>
  <p>Approved by acupressure expert</p>
</div>
<div class="perk" style="left:795px">
  <svg width="80" height="70" viewBox="0 0 80 70" fill="none" stroke="#3aa317" stroke-width="2.5"><path d="M28 50 C20 42 16 36 16 26 C16 12 28 4 40 4 C52 4 64 12 64 26 C64 36 60 42 52 50 Z"/><path d="M30 56 H50 M32 62 H48 M36 68 H44"/><path d="M34 24 C36 18 44 18 46 24 C46 30 40 32 40 40"/></svg>
  <p>A unique design based on two types of knowledge</p>
</div>

<!-- values -->
<h2 class="abs section-title values-title">Values of Our Product</h2>
<p class="abs values-text">Lorem ipsum dolor sit amet, consectetur adipiscing elit. Nam interdum ullamcorper quam, in tincidunt nibh commodo a. Aliquam malesuada&nbsp; diam vel fermentum faucibus.</p>

<svg class="abs funnel" width="1200" height="1800" viewBox="0 0 1200 1800">
  <defs>
    <marker id="hd-red" markerWidth="10" markerHeight="10" refX="1" refY="5" orient="auto"><path d="M9 1 L1 5 L9 9" fill="none" stroke="#e31226" stroke-width="1.5"/></marker>
    <marker id="hd-orange" markerWidth="10" markerHeight="10" refX="1" refY="5" orient="auto"><path d="M9 1 L1 5 L9 9" fill="none" stroke="#fd7a0b" stroke-width="1.5"/></marker>
    <marker id="hd-blue" markerWidth="10" markerHeight="10" refX="1" refY="5" orient="auto"><path d="M9 1 L1 5 L9 9" fill="none" stroke="#27a9e8" stroke-width="1.5"/></marker>
    <marker id="hd-green" markerWidth="10" markerHeight="10" refX="1" refY="5" orient="auto"><path d="M9 1 L1 5 L9 9" fill="none" stroke="#22b24b" stroke-width="1.5"/></marker>
  </defs>
  <polygon points="698,1209 1126,1209 1078,1332 746,1332" fill="#e31226"/>
  <polygon points="751,1337 1072,1337 1024,1461 799,1461" fill="#fd7a0b"/>
  <polygon points="805,1466 1016,1466 968,1590 853,1590" fill="#27a9e8"/>
  <polygon points="858,1596 964,1596 911,1722" fill="#22b24b"/>
  <text x="1058" y="1296" font-family="Lato,sans-serif" font-weight="900" font-size="66" fill="#ee5565">1</text>
  <text x="984" y="1422" font-family="Lato,sans-serif" font-weight="900" font-size="66" fill="#ffa04f">2</text>
  <text x="934" y="1552" font-family="Lato,sans-serif" font-weight="900" font-size="66" fill="#6cc6f1">3</text>
  <!-- tier icons -->
  <g fill="none" stroke="#fff" stroke-width="3"><rect x="766" y="1240" width="48" height="56" rx="8"/><circle cx="790" cy="1250" r="10"/></g>
  <g fill="#fff"><ellipse cx="780" cy="1278" rx="5" ry="8"/><ellipse cx="800" cy="1278" rx="5" ry="8"/></g>
  <g fill="#fff"><circle cx="830" cy="1364" r="7"/><path d="M816 1376 h20 l4 20 h-8 l-2 22 h-14 l-4 -22 z"/></g>
  <g fill="#fff"><circle cx="874" cy="1512" r="7"/><path d="M858 1520 l10 6 h12 l10 -6 l4 6 l-12 10 v16 h-16 v-16 l-12 -10 z"/></g>
  <g fill="#fff"><circle cx="912" cy="1625" r="6"/><path d="M898 1632 l8 5 h12 l8 -5 l3 5 l-10 9 v18 h-14 v-18 l-10 -9 z"/></g>
  <!-- arrows -->
  <line x1="713" y1="1270" x2="608" y2="1269" stroke="#e31226" stroke-width="1.5" marker-end="url(#hd-red)"/>
  <line x1="766" y1="1399" x2="661" y2="1400" stroke="#fd7a0b" stroke-width="1.5" marker-end="url(#hd-orange)"/>
  <line x1="820" y1="1532" x2="714" y2="1530" stroke="#27a9e8" stroke-width="1.5" marker-end="url(#hd-blue)"/>
  <line x1="880" y1="1661" x2="776" y2="1660" stroke="#22b24b" stroke-width="1.5" marker-end="url(#hd-green)"/>
</svg>
<p class="tier-label" style="right:615px;top:1242px;color:var(--red)">Promote Weight<br>Loss</p>
<p class="tier-label" style="right:554px;top:1372px;color:var(--orange)">Relieves Muscle and<br>Joint Pain</p>
<p class="tier-label" style="right:500px;top:1503px;color:var(--blue)">Relieves Muscle and<br>Joint Pain</p>
<p class="tier-label" style="right:439px;top:1633px;color:var(--leaf)">Increases Energy and<br>Reduces Stress</p>

<!-- cards -->
<div class="card" style="left:76px">
  <div class="card-img" role="img" aria-label="Photo of two people tying running shoes" style="background:linear-gradient(90deg,#7e7f86,#c7c8c6 45%,#b9d86a 80%,#8c8b88)"></div>
  <h3>For Men and Women</h3>
  <p>Lorem ipsum dolor sit amet, consectetur adipiscing elit. Nam interdum ullamcorper quam, in tincidunt nibh commodo..</p>
</div>
<div class="card" style="left:435px">
  <div class="card-img" role="img" aria-label="Photo of a bare foot above a blue insole on a red mat" style="background:linear-gradient(180deg,#9fb3d8 0%,#e9c8bd 40%,#ef5a64 65%,#e9424f 100%)"></div>
  <h3>One Size</h3>
  <p>Lorem ipsum dolor sit amet, consectetur adipiscing elit. Nam interdum ullamcorper quam, in tincidunt nibh commodo..</p>
</div>
<div class="card" style="left:796px">
  <div class="card-img" role="img" aria-label="Photo of hands trimming a leather insole in a workshop" style="background:linear-gradient(160deg,#3c2a20,#8a5c3f 50%,#4a3326)"></div>
  <h3>Adjustable by Cutting</h3>
  <p>Lorem ipsum dolor sit amet, consectetur adipiscing elit. Nam interdum ullamcorper quam, in tincidunt nibh commodo..</p>
</div>

<!-- features -->
<h2 class="abs section-title features-title">Features</h2>
<p class="abs features-text">Lorem ipsum dolor sit amet, consectetur adipiscing elit. Nam interdum ullamcorper quam, in tincidunt nibh commodo a.</p>
<div class="feature" style="left:88px;top:2540px">
  <svg width="46" height="46" viewBox="0 0 46 46" fill="none" stroke="#333" stroke-width="5"><path d="M30 10 L14 18 C6 22 6 34 14 38 C22 42 30 36 34 28"/></svg>
  <span>Powerful Magnet In<br>Tourmaline</span>
</div>
<div class="feature" style="left:376px;top:2540px">
  <svg width="40" height="40" viewBox="0 0 40 40" fill="#333"><path d="M22 4 C32 4 38 12 34 22 L24 36 C20 40 10 38 8 30 L18 14 C20 10 18 8 14 10 L10 12 C12 6 16 4 22 4 Z"/></svg>
  <span>Flexible And<br>Light</span>
</div>
<div class="feature" style="left:75px;top:2637px">
  <svg width="60" height="36" viewBox="0 0 60 36" fill="#333"><path d="M2 14 C10 14 18 10 24 4 L32 10 C38 14 48 16 56 20 C60 24 58 30 54 30 L6 28 C2 26 0 20 2 14 Z"/></svg>
  <span>For All Type Of<br>Shoes</span>
</div>
<div class="feature" style="left:374px;top:2643px">
  <svg width="42" height="36" viewBox="0 0 42 36" fill="none" stroke="#333" stroke-width="3"><path d="M4 14 H38 M4 22 H38"/><path d="M10 4 C6 10 14 14 10 20 C6 26 14 30 10 34 M21 4 C17 10 25 14 21 20 C17 26 25 30 21 34 M32 4 C28 10 36 14 32 20 C28 26 36 30 32 34"/></svg>
  <span>Breathable</span>
</div>
<div class="features-photo" role="img" aria-label="Photo of a foot stepping onto a dark insole held by gloved hands"></div>

<!-- services band -->
<div class="abs band"></div>
<div class="service" style="left:60px">
  <svg width="62" height="52" viewBox="0 0 62 52" fill="none" stroke="#fff" stroke-width="2"><path d="M2 8 H40 V40 H2 Z M40 18 H52 L60 28 V40 H40"/><circle cx="14" cy="44" r="5"/><circle cx="48" cy="44" r="5"/></svg>
  <h4>Free Shipping</h4>
  <p>Mauris ultrices tellus lacus, eget aliquam orci vestibulum</p>
</div>
<div class="service" style="left:329px">
  <svg width="62" height="52" viewBox="0 0 62 52" fill="none" stroke="#fff" stroke-width="2"><ellipse cx="24" cy="20" rx="21" ry="15"/><path d="M10 32 L6 44 L20 34"/><path d="M44 16 C54 18 60 24 58 32 C56 38 52 40 52 40 L56 50 L44 42 C36 42 30 38 28 34"/></svg>
  <h4>Customer Service</h4>
  <p>Mauris ultrices tellus lacus, eget aliquam orci vestibulum</p>
</div>
<div class="service" style="left:600px">
  <svg width="62" height="60" viewBox="0 0 62 60" fill="none" stroke="#fff" stroke-width="2.5"><path d="M31 2 V58 M42 16 C42 10 36 8 31 8 C24 8 20 12 20 18 C20 30 44 26 44 40 C44 48 38 52 31 52 C24 52 18 48 18 42"/></svg>
  <h4>Money Back Guarantee</h4>
  <p>Mauris ultrices tellus lacus, eget aliquam orci vestibulum</p>
</div>
<div class="service" style="left:869px">
  <svg width="62" height="52" viewBox="0 0 62 52" fill="none" stroke="#fff" stroke-width="2"><rect x="13" y="22" width="36" height="28" rx="3"/><path d="M20 22 V14 C20 4 42 4 42 14 V22"/><path d="M31 32 V40"/></svg>
  <h4>Safe Payment</h4>
  <p>Mauris ultrices tellus lacus, eget aliquam orci vestibulum</p>
</div>

<!-- footer -->
<div class="brand" style="left:75px;top:3072px">
  <span class="brand-dot" style="width:36px;height:36px"></span>
  <div><div class="brand-name" style="font-size:32px">StrideLeaf</div><div class="brand-tag" style="font-size:13px">L’essayer c’est l’adopter !</div></div>
</div>
<p class="abs foot-copy">Copyright © 2019 Company Name<br>All Right Reserved</p>
<div class="foot-col" style="left:434px">
  <h5>LEARN MORE</h5>
  <ul><li>FAQ</li><li>User Manual</li></ul>
</div>
<div class="foot-col" style="left:641px">
  <h5>SUPPORT</h5>
  <ul>
    <li><svg width="12" height="12" viewBox="0 0 12 12" fill="#333"><path d="M2 1 L4 1 L5 4 L3.5 5 C4.5 7 5 7.5 7 8.5 L8 7 L11 8 V10 C11 11 10 11 9 11 C4 10 1 7 1 3 C1 2 1 1 2 1 Z"/></svg>1-800-555-0142</li>
    <li><svg width="12" height="10" viewBox="0 0 12 10" fill="#333"><path d="M0 0 H12 V10 H0 Z"/><path d="M0 0 L6 5 L12 0" fill="none" stroke="#fff"/></svg>hello@strideleaf.example</li>
  </ul>
</div>
<div class="foot-col" style="left:898px">
  <h5>FOLLOW US</h5>
  <div class="socials"><span></span><span></span><span></span><span></span><span></span></div>
</div>
<span class="abs page-mark">X10</span>

</body>
</html>
```